Roofing Company Modern look

I want a modern and sophisticated look for our roofing business.

Our address is :

5217 Mallow Creek Ln
Orlando, Fl 32825

(407)-583-2196

www.HarborlineRoofsFl.com

I also want to make sure on the back there is a spot to put
Project Manager Name :

Number:

Because the cards will be used by all sales people

Project Manager Name :

Also there are accreditation we have logos are uploaded here as well that I would like maybe on the back of card as well

I also want to highlight our special attributions or trades:

Residential & Commercial
Fully Insured
License # CCC7482913
Insurance Claims
Serving Central Florida Since 1992
Free Estimates

Contact Information for Business Card

Our address is :

5217 Mallow Creek Ln
Orlando, Fl 32825

(407)-583-2196

Project Manager Name :

Residential & Commercial
Fully Insured
License # CCC7482913
Insurance Claims
Free Estimates

Font styles to use
Serif
Sans Serif

Colors
3176b5

Requirements
Must have
• Must have royal blue like my logo grey and black are the colors I like

```html
<!DOCTYPE html>
<html lang="en">
<head>
<meta charset="utf-8">
<title>Harborline Roofing &amp; Gutters – Business Card</title>
<link href="https://fonts.googleapis.com/css2?family=Arimo:wght@400;700&display=swap" rel="stylesheet">
<style>
  :root {
    --stage: #0b0b0c;
    --card: #26272a;
    --card-deep: #1d1e20;
    --royal: #3176b5;
    --royal-bright: #2f8be0;
    --text-light: #d9dadc;
    --text-muted: #a9abae;
    --rule: #55575b;
    --badge-navy: #1f4f9a;
    --badge-red: #d21f26;
    --badge-white: #f4f5f7;
  }
  * { box-sizing: border-box; margin: 0; padding: 0; }
  html, body {
    width: 1200px; height: 820px; overflow: hidden;
    background: var(--stage);
    font-family: "Arimo", Arial, sans-serif;
  }
  .stage {
    width: 1200px; height: 820px;
    display: flex; align-items: center; justify-content: center; gap: 40px;
  }
  .card {
    position: relative;
    width: 540px; height: 309px;
    background: linear-gradient(160deg, var(--card) 0%, var(--card-deep) 100%);
    border-bottom: 4px solid var(--royal);
    border-left: 2px solid var(--royal);
    overflow: hidden;
  }

  /* Front */
  .brand {
    position: absolute; left: 150px; top: 62px;
    display: flex; align-items: center; gap: 14px;
  }
  .brand-dot {
    width: 46px; height: 46px; border-radius: 50%;
    background: var(--royal-bright);
  }
  .brand-name {
    color: var(--royal-bright);
    font-weight: 700; text-transform: uppercase;
    font-size: 26px; letter-spacing: 2px; line-height: 1.05;
  }
  .brand-name small { display: block; font-size: 12px; letter-spacing: 1.6px; }
  .divider {
    position: absolute; left: 212px; right: 30px; top: 178px;
    height: 1px; background: var(--rule);
  }
  .rep-name {
    position: absolute; left: 40px; top: 166px;
    color: var(--royal-bright);
    font-size: 22px; letter-spacing: 1px; text-transform: uppercase;
  }
  .contact {
    position: absolute; left: 40px; bottom: 34px;
    list-style: none; display: grid; gap: 8px;
  }
  .contact li {
    display: flex; align-items: center; gap: 10px;
    color: var(--text-light); font-size: 16px;
  }
  .contact svg { width: 16px; height: 16px; fill: var(--royal-bright); }
  .contact .accent { color: var(--royal-bright); }
  .address {
    position: absolute; right: 30px; top: 198px;
    text-align: right; color: var(--text-muted);
    font-size: 16px; line-height: 1.3;
  }

  /* Back */
  .back-glow {
    position: absolute; inset: 0;
    background: radial-gradient(ellipse at 25% 70%, rgba(255,255,255,0.07), transparent 60%);
  }
  .services {
    position: absolute; left: 230px; top: 40px;
    list-style: none; display: grid; gap: 5px;
  }
  .services li {
    color: var(--text-light); font-size: 14px;
    display: flex; align-items: center; gap: 9px;
  }
  .services li::before {
    content: ""; width: 5px; height: 5px; border-radius: 50%;
    background: var(--royal-bright);
  }
  .badge { position: absolute; }
  .badge-applicator {
    left: 245px; top: 210px; width: 76px; height: 40px;
    background: var(--badge-navy); border: 2px solid var(--badge-white);
  }
  .badge-authorized {
    left: 290px; top: 258px; width: 120px; height: 30px;
    background: var(--badge-white); border-left: 26px solid var(--badge-red);
  }
  .badge-accredited {
    left: 440px; top: 170px; width: 62px; height: 80px;
    background: var(--badge-white); border-radius: 8px;
    border: 3px solid var(--badge-navy);
  }
</style>
</head>
<body>
<main class="stage">

  <section class="card card-front">
    <div class="brand">
      <span class="brand-dot"></span>
      <p class="brand-name">Harborline<small>Roofing &amp; Gutters LLC</small></p>
    </div>
    <div class="divider"></div>
    <p class="rep-name">Marcus Delaney</p>
    <ul class="contact">
      <li>
        <svg viewBox="0 0 24 24" aria-hidden="true"><path d="M6.6 10.8a15.1 15.1 0 0 0 6.6 6.6l2.2-2.2a1 1 0 0 1 1-.25 11.4 11.4 0 0 0 3.6.57 1 1 0 0 1 1 1V20a1 1 0 0 1-1 1A17 17 0 0 1 3 4a1 1 0 0 1 1-1h3.5a1 1 0 0 1 1 1c0 1.25.2 2.46.57 3.6a1 1 0 0 1-.25 1z"/></svg>
        (407)-583-2196
      </li>
      <li>
        <svg viewBox="0 0 24 24" aria-hidden="true"><path d="M12 2a10 10 0 1 0 0 20 10 10 0 0 0 0-20zm6.9 6h-2.9a15.6 15.6 0 0 0-1.4-3.6A8 8 0 0 1 18.9 8zM12 4a14 14 0 0 1 1.9 4h-3.8A14 14 0 0 1 12 4zM4.3 14a8 8 0 0 1 0-4h3.4a16.5 16.5 0 0 0 0 4zm.8 2h2.9a15.6 15.6 0 0 0 1.4 3.6A8 8 0 0 1 5.1 16zM8 8H5.1a8 8 0 0 1 4.3-3.6A15.6 15.6 0 0 0 8 8zm4 12a14 14 0 0 1-1.9-4h3.8A14 14 0 0 1 12 20zm2.3-6H9.7a14.7 14.7 0 0 1 0-4h4.6a14.7 14.7 0 0 1 0 4zm.3 5.6a15.6 15.6 0 0 0 1.4-3.6h2.9a8 8 0 0 1-4.3 3.6zM16.3 14a16.5 16.5 0 0 0 0-4h3.4a8 8 0 0 1 0 4z"/></svg>
        <span>www.<span class="accent">HarborlineRoofsFl</span>.com</span>
      </li>
    </ul>
    <p class="address">5217 Mallow Creek Ln<br>Orlando, Fl 32825</p>
  </section>

  <section class="card card-back">
    <div class="back-glow"></div>
    <ul class="services">
      <li>Residential &amp; Commercial</li>
      <li>Fully Insured</li>
      <li>License # CCC7482913</li>
      <li>Insurance Claims</li>
      <li>Serving Central Florida Since 1992</li>
      <li>Free Estimates</li>
    </ul>
    <div class="badge badge-applicator" role="img" aria-label="Shingle applicator certification badge"></div>
    <div class="badge badge-authorized" role="img" aria-label="Authorized roofing contractor badge"></div>
    <div class="badge badge-accredited" role="img" aria-label="Accredited business rating badge"></div>
  </section>

</main>
</body>
</html>
```